Business Card Design

Looking for business card designs for a new business. there will be two cards of the same design (both lots of information below in contact info). We would like the logo diagonally across the card with the information split above and below the logo similar to sketch. happy to look at similar alternatives
Please use same colours as in logo design

Industry/Entity Type

Business

Contact Information for Business Card

Dwight Halloran
mob - 0491 738 204
ph - 02 6148 3920
fax - 02 6148 3975
email - dwight@kestrelbeams.com.au
14 Larkmoor Road, Taminda NSW 2340

Colin Marchetti
mob - 0438 912 557
ph - 02 6148 3920
fax - 02 6148 3975
email - colin@kestrelbeams.com.au

```html
<!DOCTYPE html>
<html lang="en">
<head>
<meta charset="utf-8">
<title>Kestrel Beams – Business Cards</title>
<link href="https://fonts.googleapis.com/css2?family=Open+Sans:wght@400;600;700&display=swap" rel="stylesheet">
<style>
  :root {
    --teal: #0e7d80;
    --ink: #111111;
    --paper: #ffffff;
    --night: #000000;
    --stage: #e9e6e2;
    --rule: #555555;
  }
  * { margin: 0; padding: 0; box-sizing: border-box; }
  html, body { width: 1200px; height: 1191px; overflow: hidden; }
  body {
    position: relative;
    background: var(--stage);
    font-family: "Open Sans", Arial, sans-serif;
  }
  .card {
    position: absolute;
    width: 945px;
    height: 540px;
    overflow: hidden;
  }
  .card--front { left: 28px; top: 35px; background: var(--paper); }
  .card--back { left: 237px; top: 602px; background: var(--night); }

  .corner-peel { position: absolute; inset: 0; }

  .holder-name {
    position: absolute;
    right: 22px;
    top: 52px;
    color: var(--paper);
    font-weight: 700;
    font-size: 28px;
  }

  .brand {
    position: absolute;
    display: flex;
    align-items: center;
    gap: 16px;
    font-weight: 700;
    line-height: 1;
    white-space: nowrap;
  }
  .brand__mark { background: var(--teal); flex: none; }
  .card--front .brand { left: 35px; top: 195px; font-size: 70px; color: var(--ink); letter-spacing: -1px; }
  .card--front .brand__mark { width: 50px; height: 50px; }
  .card--back .brand { left: 0; right: 0; justify-content: center; top: 205px; font-size: 90px; color: var(--teal); letter-spacing: -1px; }
  .card--back .brand__mark { width: 64px; height: 64px; }

  .contact-list {
    position: absolute;
    left: 30px;
    top: 380px;
    list-style: none;
    font-size: 23px;
    color: var(--ink);
  }
  .contact-list li {
    display: flex;
    align-items: center;
    gap: 8px;
    height: 36px;
  }
  .contact-list svg { width: 20px; height: 20px; fill: var(--teal); flex: none; }

  .address {
    position: absolute;
    left: 467px;
    top: 445px;
    padding-left: 14px;
    border-left: 2px solid var(--rule);
    font-size: 23px;
    font-style: normal;
    line-height: 38px;
    color: var(--ink);
  }

  .web {
    position: absolute;
    left: 0; right: 0;
    top: 425px;
    text-align: center;
    color: var(--paper);
    font-size: 30px;
    letter-spacing: 2px;
  }
  .web strong { font-weight: 600; }
</style>
</head>
<body>

<section class="card card--front" aria-label="Business card front">
  <svg class="corner-peel" viewBox="0 0 945 540" aria-hidden="true">
    <defs>
      <linearGradient id="peel-shade" x1="0" y1="0" x2="1" y2="1">
        <stop offset="0" stop-color="#000"/>
        <stop offset="0.55" stop-color="#333"/>
        <stop offset="1" stop-color="#fff"/>
      </linearGradient>
    </defs>
    <polygon points="443,0 945,0 945,200" fill="var(--teal)"/>
    <path d="M443,0 C560,90 700,200 865,340 C880,300 905,240 945,200 Z" fill="url(#peel-shade)"/>
  </svg>

  <div class="holder-name">Colin Marchetti</div>

  <div class="brand"><span class="brand__mark"></span>Kestrel Beams</div>

  <ul class="contact-list">
    <li><svg viewBox="0 0 20 20"><path d="M4 2l4 1 1 4-2 2c1 2 3 4 5 5l2-2 4 1 1 4-2 1C9 18 2 11 2 4z"/></svg>02 6148 3920</li>
    <li><svg viewBox="0 0 20 20"><path d="M6 1h8a1 1 0 011 1v16a1 1 0 01-1 1H6a1 1 0 01-1-1V2a1 1 0 011-1zm1 3v9h6V4z"/></svg>0438 912 557</li>
    <li><svg viewBox="0 0 20 20"><path d="M5 2h9v5h3a2 2 0 012 2v7H1V9a2 2 0 012-2h2zm2 2v3h5V4zM4 11v2h12v-2z"/></svg>02 6148 3975</li>
    <li><svg viewBox="0 0 20 20"><path d="M1 8l9-5 9 5v9H1zm2 1l7 4 7-4-7-4z"/></svg>colin@kestrelbeams.com.au</li>
  </ul>

  <address class="address">14 Larkmoor Road<br>Corrabin NSW 2395</address>
</section>

<section class="card card--back" aria-label="Business card back">
  <div class="brand"><span class="brand__mark"></span>Kestrel Beams</div>
  <div class="web">www.<strong>kestrelbeams</strong>.com.au</div>
</section>

</body>
</html>
```